Business Card Design - ChoiceCraft

Looking for creative, modern design, two sided for ChoiceCraft that is consistent with color and feel of website www.choicecraftpro.net.
Updates

Back of card will be used to promote products or have a quote revolving around decisions, change, leadership, innovation, creativity. Back should also have space to promote website, but optional to use the icon. Front of the card will need to use the icon and have standard place for name, job title, phone and email. We are not looking to put a mailing address or fax. Also want space to place a few words/phrase explaining what we do...such as individual growth and organizational development or tools, training, information...in addition, want the facebook icon small on the front somewhere as we are also on facebook.

Vector file uploaded of icon.

Target Market(s)

Professional coaching for individual growth and organizational development

Industry/Entity Type

Business

Requirements
Must have
• Icon...see attached.

```html
<!DOCTYPE html>
<html lang="en">
<head>
<meta charset="utf-8">
<title>ChoiceCraft – Business Card</title>
<link rel="stylesheet" href="https://fonts.googleapis.com/css2?family=Arimo:wght@400;700&family=Tinos:wght@400;700&display=swap">
<style>
  :root {
    --bg: #d9dadc;
    --white: #ffffff;
    --brand-blue: #1e8fd0;
    --navy: #2a3270;
    --band-deep: #1c4f9c;
    --band-mid: #2f7ccc;
    --band-light: #5cb8ec;
    --back-deep: #1a7ccc;
    --back-light: #3ea7e6;
    --mark-grey: #c9d3dc;
  }
  * { margin: 0; padding: 0; box-sizing: border-box; }
  html, body { width: 1200px; height: 1079px; overflow: hidden; }
  body { background: var(--bg); position: relative; }

  .card { position: absolute; width: 802px; overflow: hidden; box-shadow: 0 2px 6px rgba(0,0,0,.25); }

  /* Front */
  .card-front { left: 67px; top: 66px; height: 456px; background: var(--white); }
  .brand-mark { position: absolute; left: 179px; top: 63px; width: 140px; height: 140px; border-radius: 50%;
    background: radial-gradient(circle at 40% 35%, #f3f6f9, var(--mark-grey) 70%, #8fb4d6); }
  .brand-name { position: absolute; left: 351px; top: 108px; font: 700 37px Arimo, sans-serif; color: var(--brand-blue); letter-spacing: .2px; }
  .person { position: absolute; left: 0; width: 100%; top: 252px; text-align: center; font: 700 27px Tinos, serif; color: var(--navy); }
  .person .title { font-weight: 400; font-size: 20px; }
  .band { position: absolute; left: 0; top: 0; width: 802px; height: 456px; }
  .contact { position: absolute; left: 0; width: 100%; text-align: center; font: 400 19px Tinos, serif; color: var(--white); }
  .contact.phone { top: 334px; }
  .contact.links { top: 357px; }
  .contact.links span { margin: 0 6px; }
  .social-dot { display: inline-block; width: 11px; height: 11px; background: var(--band-light); margin-right: 5px; vertical-align: 1px; }
  .tagline { position: absolute; left: 0; width: 100%; top: 395px; text-align: center; font: 400 19px/23px Tinos, serif; color: var(--white); }

  /* Back */
  .card-back { left: 328px; top: 559px; height: 459px;
    background: radial-gradient(ellipse at 72% 60%, var(--back-light), var(--back-deep) 75%); }
  .back-mark { position: absolute; left: 565px; top: 266px; width: 168px; height: 168px; border-radius: 50%;
    background: rgba(255,255,255,.22); }
  .quotes { position: absolute; left: 53px; top: 38px; list-style: none; }
  .quote { position: relative; padding-left: 29px; height: 81px; color: var(--white); font-family: Arimo, sans-serif; }
  .quote-text { font-size: 20px; font-weight: 400; }
  .quote-text::before { content: "\201C"; position: absolute; left: 0; top: -6px; font: 700 36px Tinos, serif; }
  .quote-text::after { content: "\201D"; font: 700 36px Tinos, serif; position: relative; top: 12px; margin-left: 2px; line-height: 0; }
  .quote-author { display: block; font-size: 20px; font-weight: 700; margin-top: 4px; }
</style>
</head>
<body>

<section class="card card-front" aria-label="Card front">
  <svg class="band" viewBox="0 0 802 456" aria-hidden="true">
    <defs>
      <linearGradient id="bandFill" x1="0" y1="0" x2="0" y2="1">
        <stop offset="0" stop-color="var(--band-mid)"/>
        <stop offset="1" stop-color="var(--band-deep)"/>
      </linearGradient>
      <radialGradient id="bandGlow" cx="0.5" cy="0.2" r="0.5">
        <stop offset="0" stop-color="var(--band-light)" stop-opacity=".8"/>
        <stop offset="1" stop-color="var(--band-light)" stop-opacity="0"/>
      </radialGradient>
    </defs>
    <path d="M0 378 Q401 250 802 378 L802 456 L0 456 Z" fill="url(#bandFill)"/>
    <path d="M0 378 Q401 250 802 378 L802 456 L0 456 Z" fill="url(#bandGlow)"/>
    <path d="M40 368 Q401 262 762 368" fill="none" stroke="var(--band-light)" stroke-width="3"/>
  </svg>
  <div class="brand-mark" aria-hidden="true"></div>
  <div class="brand-name">ChoiceCraft</div>
  <div class="person">Your Name, <span class="title">Title</span></div>
  <div class="contact phone">✆ 123-456-789</div>
  <div class="contact links">
    <span>✉ info@choicecraftpro.net</span>
    <span>www.choicecraftpro.net</span>
    <span><i class="social-dot"></i>/choicecraftpro</span>
  </div>
  <p class="tagline">Supporting individual growth<br>and organizational development, or tools, training, information</p>
</section>

<section class="card card-back" aria-label="Card back">
  <div class="back-mark" aria-hidden="true"></div>
  <ul class="quotes">
    <li class="quote"><span class="quote-text">Try not to become a man of success, but rather a man of value.</span><span class="quote-author">- Alden Ferris</span></li>
    <li class="quote"><span class="quote-text">The only constant is change.</span><span class="quote-author">- Halvor Dane</span></li>
    <li class="quote"><span class="quote-text">We are what we repeatedly do. Excellence is not an act, it is a habit.</span><span class="quote-author">- Marcus Evander</span></li>
    <li class="quote"><span class="quote-text">Simplicity is the ultimate sophistication.</span><span class="quote-author">- Lorenzo Vell</span></li>
    <li class="quote"><span class="quote-text">Life is not fair - get used to it.</span><span class="quote-author">- Bram Tolliver</span></li>
  </ul>
</section>

</body>
</html>
```